BOLD & MINIMALIST DESIGN NEEDED

We want a very bold but minimalistic business card design that is impactful and utilizes both sides of the business card. Our current logo is included for your use.

We want bold fonts and good use of negative space. We don't want the logo to overpower the design.

Target Market(s)

Professionals who are building new commercial buildings.

Industry/Entity Type

Construction

Contact Information for Business Card

Name, Title, email, office phone, cell phone, website

Font styles to use
Serif
Sans Serif

Requirements
Must have
• Bold design!

```html
<!DOCTYPE html>
<html lang="en">
<head>
<meta charset="utf-8">
<title>Ridgeline Build – Business Card</title>
<link href="https://fonts.googleapis.com/css2?family=Arimo:wght@400;700&display=swap" rel="stylesheet">
<style>
  :root {
    --backdrop: #dcdcdc;
    --card-white: #ffffff;
    --ink: #111111;
    --text-grey: #555555;
    --brand-green: #7dc242;
    --brand-green-light: #a6d86a;
    --card-dark: #333333;
    --card-dark-top: #3d3d3d;
    --divider: #c8c8c8;
  }
  * { box-sizing: border-box; margin: 0; padding: 0; }
  html, body {
    width: 1200px; height: 1200px; overflow: hidden;
    background: var(--backdrop);
    font-family: "Arimo", Arial, sans-serif;
  }
  .canvas { position: relative; width: 1200px; height: 1200px; }
  .card {
    position: absolute; left: 265px; width: 687px; height: 394px;
    border-radius: 20px; overflow: hidden;
  }
  .card-front { top: 159px; background: var(--card-white); }
  .card-back {
    top: 653px;
    background: linear-gradient(180deg, var(--card-dark-top), var(--card-dark));
  }
  .front-swoosh { position: absolute; left: 0; top: 0; width: 687px; height: 394px; }
  .brand-front {
    position: absolute; left: 100px; top: 222px; width: 240px;
    display: flex; align-items: center; justify-content: center; gap: 10px;
    font-weight: 700; font-size: 30px; color: var(--ink); letter-spacing: 0.5px;
    transform: translateY(-50%);
  }
  .brand-mark { width: 16px; height: 16px; background: var(--brand-green); flex: none; }
  .divider {
    position: absolute; left: 354px; top: 107px; width: 1px; height: 154px;
    background: var(--divider);
  }
  .contact { position: absolute; left: 382px; top: 120px; }
  .contact-name { font-weight: 700; font-size: 26px; color: var(--ink); letter-spacing: 0.5px; }
  .contact-title { font-size: 15px; color: var(--brand-green); margin-top: 3px; }
  .contact-list { list-style: none; margin-top: 18px; }
  .contact-list li {
    display: flex; align-items: center; gap: 10px;
    font-size: 16px; color: var(--text-grey); height: 21px;
  }
  .contact-list svg { width: 15px; height: 15px; flex: none; }
  .website {
    position: absolute; left: 0; width: 100%; top: 356px; text-align: center;
    font-size: 16px; color: var(--card-white);
  }
  .brand-back {
    position: absolute; left: 0; top: 0; width: 100%; height: 100%;
    display: flex; align-items: center; justify-content: center; gap: 18px;
    font-weight: 700; font-size: 58px; color: var(--card-white); letter-spacing: 1px;
  }
  .brand-back .brand-mark { width: 30px; height: 30px; }
</style>
</head>
<body>
<div class="canvas">
  <section class="card card-front">
    <svg class="front-swoosh" viewBox="0 0 687 394" aria-hidden="true">
      <defs>
        <linearGradient id="greenBand" x1="0" x2="1" y1="0" y2="0">
          <stop offset="0" stop-color="#6fb83a"/>
          <stop offset="0.45" stop-color="#a6d86a"/>
          <stop offset="1" stop-color="#79c23c"/>
        </linearGradient>
      </defs>
      <path d="M10 394 Q 353 300 680 394 Z" fill="#111"/>
      <path d="M20 394 Q 353 318 670 394 Z" fill="url(#greenBand)"/>
    </svg>

    <div class="brand-front"><span class="brand-mark"></span>Ridgeline Build</div>
    <div class="divider"></div>

    <div class="contact">
      <h1 class="contact-name">DANIEL REYES</h1>
      <p class="contact-title">President</p>
      <ul class="contact-list">
        <li>
          <svg viewBox="0 0 16 16" aria-hidden="true"><path fill="#111" d="M3.5 1.5l2.5 0 1 3.5-1.6 1.2a8 8 0 0 0 4.4 4.4L11 9l3.5 1v2.5c0 1-1 2-2 2A11 11 0 0 1 1.5 3.5c0-1 1-2 2-2z"/></svg>
          555-210-4871
        </li>
        <li>
          <svg viewBox="0 0 16 16" aria-hidden="true"><rect x="4" y="1" width="8" height="14" rx="1.5" fill="none" stroke="#111" stroke-width="1.6"/><rect x="7" y="12" width="2" height="1.4" fill="#111"/></svg>
          555-210-9362
        </li>
        <li>
          <svg viewBox="0 0 16 16" aria-hidden="true"><rect x="1" y="4" width="14" height="9" fill="#111"/><path d="M1.5 4.5L8 9.5l6.5-5" fill="none" stroke="#fff" stroke-width="1.3"/></svg>
          info@ridgelinebuild.com
        </li>
      </ul>
    </div>

    <p class="website">www.ridgelinebuild.com</p>
  </section>

  <section class="card card-back">
    <div class="brand-back"><span class="brand-mark"></span>Ridgeline Build</div>
  </section>
</div>
</body>
</html>
```